we can communicate on this, but i want to follow the approach we took on Pellew|Marsh & Quinlan but i feel the card front needs the black background and the platinum and gold logo. The back? I am open. we can use the same info from PM&Q. Velmont Arc is an enhanced equity investment fund - basically a very exclusive boutique hedge fund that uses only stock options. very advanced things. hope you are interested

Contact Information for Business Card

Dr. Lewis T. Brennick, CFA
Scientifique de fusée financière
701.555.0143
LTBquant47@mailvantor.com

4718 Willow Creek Bend W.
West Fargo, ND 58078

No web site

Colors

Designer to choose colors to be used in the design.

Requirements
Nice to have
• I tend to prefer the most visible applications of the logo to include logo and name, the logo version with a black background and the gold and platinum components separated by the black. I see this working well for a single side (logo and name - this is card front to me).
• I am fairly open to other treatments on the reverse side with the data. To me, it makes sense to have a different color rendition of the logo on the reverse and it may be a muted black tone on tone or an oversized portion that would have spot UV. Or, the reverse may play with colors and layout
Should not have
• Other colors = no no
• Decorative font

```html
<!DOCTYPE html>
<html lang="en">
<head>
<meta charset="utf-8">
<title>Velmont Arc — Business Card</title>
<link rel="stylesheet" href="https://fonts.googleapis.com/css2?family=Montserrat:wght@600&family=Roboto:ital,wght@0,400;0,500;0,700;1,400&display=swap">
<style>
  :root {
    --backdrop: #1b1b1c;
    --card: #141415;
    --card-edge: #262628;
    --platinum: #c9c9cb;
    --gold: #d4ad2f;
    --ink: #f2f2f2;
    --rule: #e6e6e6;
  }
  * { margin: 0; padding: 0; box-sizing: border-box; }
  html, body {
    width: 1200px; height: 800px; overflow: hidden;
    background: var(--backdrop);
  }
  .canvas {
    position: relative; width: 1200px; height: 800px;
    display: flex; flex-direction: column; align-items: center; justify-content: center; gap: 40px;
  }
  .card {
    position: relative; width: 560px; height: 320px;
    background: var(--card);
    border: 1px solid var(--card-edge);
    box-shadow: 0 10px 30px rgba(0,0,0,.45);
  }

  /* Front */
  .card-front { display: flex; flex-direction: column; align-items: center; justify-content: center; gap: 22px; }
  .front-mark { width: 130px; height: 130px; border-radius: 50%; background: var(--platinum); }
  .front-name {
    font-family: "Montserrat", sans-serif; font-weight: 600;
    font-size: 40px; letter-spacing: 2px; color: var(--platinum);
    text-transform: uppercase;
  }

  /* Back */
  .card-back { font-family: "Roboto", sans-serif; color: var(--ink); }
  .back-brand {
    position: absolute; left: 58px; top: 96px; width: 160px;
    display: flex; flex-direction: column; align-items: center; gap: 12px;
  }
  .back-mark { width: 58px; height: 58px; border-radius: 50%; background: var(--gold); }
  .back-name {
    font-family: "Montserrat", sans-serif; font-weight: 600;
    font-size: 20px; letter-spacing: .5px; color: var(--ink); text-transform: uppercase;
    white-space: nowrap;
  }
  .divider { position: absolute; left: 246px; top: 78px; width: 1px; height: 134px; background: var(--rule); }
  .person { position: absolute; left: 272px; top: 78px; }
  .person-name { font-size: 21px; font-weight: 700; color: var(--gold); white-space: nowrap; }
  .person-name .prefix { font-size: 15px; font-weight: 500; }
  .person-name .credential { font-size: 11px; font-weight: 500; vertical-align: super; }
  .person-title { font-size: 12.5px; font-style: italic; margin-top: 3px; }
  .contacts { list-style: none; margin-top: 26px; display: flex; flex-direction: column; gap: 7px; }
  .contacts li { display: flex; align-items: center; gap: 9px; font-size: 13px; white-space: nowrap; }
  .icon { width: 12px; height: 12px; flex: none; fill: var(--gold); }
  .address {
    position: absolute; left: 0; right: 0; bottom: 36px;
    display: flex; justify-content: center; align-items: center; gap: 8px; font-size: 13.5px;
    white-space: nowrap;
  }
  .address .icon { width: 13px; height: 15px; }
</style>
</head>
<body>
<main class="canvas">

  <section class="card card-front" aria-label="Card front">
    <div class="front-mark" aria-hidden="true"></div>
    <div class="front-name">Velmont Arc</div>
  </section>

  <section class="card card-back" aria-label="Card back">
    <div class="back-brand">
      <div class="back-mark" aria-hidden="true"></div>
      <div class="back-name">Velmont Arc</div>
    </div>

    <div class="divider" aria-hidden="true"></div>

    <div class="person">
      <p class="person-name"><span class="prefix">Dr.</span> Lewis T. Brennick, <span class="credential">CFA</span></p>
      <p class="person-title">Scientifique de fusée financière</p>
      <ul class="contacts">
        <li>
          <svg class="icon" viewBox="0 0 12 12" aria-hidden="true"><path d="M3 0h6a1 1 0 0 1 1 1v10a1 1 0 0 1-1 1H3a1 1 0 0 1-1-1V1a1 1 0 0 1 1-1zm.6 1.4v8.2h4.8V1.4z"/></svg>
          701.555.0143
        </li>
        <li>
          <svg class="icon" viewBox="0 0 12 12" aria-hidden="true"><path d="M0 2.5h12v7H0zM1 3.3l5 3.5 5-3.5v-.1H1z"/></svg>
          LTBquant47@mailvantor.com
        </li>
      </ul>
    </div>

    <p class="address">
      <svg class="icon" viewBox="0 0 12 15" aria-hidden="true"><path d="M6 0a6 6 0 0 1 6 6c0 4-6 9-6 9S0 10 0 6a6 6 0 0 1 6-6zm0 3.5a2.5 2.5 0 1 0 0 5 2.5 2.5 0 0 0 0-5z"/></svg>
      4718 Willow Creek Bend W., West Fargo, ND 58078
    </p>
  </section>

</main>
</body>
</html>
```